The Plate Compass

Cutting Through the Noise to What Actually Works.

Nutrition book

Target Market(s)

People looking to be or get healthy and eat right.

```html
<!DOCTYPE html>
<html lang="en">
<head>
<meta charset="utf-8">
<title>The Plate Compass — Book Cover</title>
<link href="https://fonts.googleapis.com/css2?family=Archivo:ital,wght@0,400;0,500;0,600;0,700;0,800;0,900;1,400;1,500&display=swap" rel="stylesheet">
<style>
  :root {
    --paper: #ffffff;
    --ink: #363534;
    --accent: #e0703c;
    --noise-dark: #9a9a9a;
    --noise-mid: #adadad;
    --noise-light: #c6c6c6;
    --subtitle: #7a7a7a;
    --byline: #9b9b9b;
  }
  html, body {
    margin: 0;
    padding: 0;
    overflow: hidden;
    background: var(--paper);
  }
  .cover {
    position: relative;
    width: 811px;
    height: 1200px;
    background: var(--paper);
    overflow: hidden;
    font-family: "Archivo", sans-serif;
  }
  .buzzword {
    position: absolute;
    margin: 0;
    white-space: nowrap;
    line-height: 1;
    color: var(--noise-mid);
    font-weight: 500;
    transform-origin: left center;
  }
  .buzzword.strong { color: var(--noise-dark); font-weight: 800; }
  .buzzword.bold { font-weight: 700; }
  .buzzword.faint { color: var(--noise-light); font-weight: 400; }
  .buzzword.caps { letter-spacing: 0.02em; }

  .rule-wide {
    position: absolute;
    left: 64px;
    top: 574px;
    width: 680px;
    height: 4px;
    background: var(--accent);
  }
  .title-kicker {
    position: absolute;
    left: 0;
    top: 648px;
    width: 100%;
    margin: 0;
    text-align: center;
    color: var(--accent);
    font-size: 31px;
    font-weight: 800;
    letter-spacing: 0.3em;
    text-indent: 0.3em;
    line-height: 1;
  }
  .title-main {
    position: absolute;
    left: 0;
    top: 688px;
    width: 100%;
    margin: 0;
    text-align: center;
    color: var(--ink);
    font-size: 88px;
    font-weight: 900;
    line-height: 92px;
    letter-spacing: 0.005em;
  }
  .title-main span { display: block; }
  .rule-short {
    position: absolute;
    left: 314px;
    top: 893px;
    width: 180px;
    height: 3px;
    background: var(--accent);
  }
  .subtitle {
    position: absolute;
    left: 0;
    top: 950px;
    width: 100%;
    margin: 0;
    text-align: center;
    color: var(--subtitle);
    font-size: 29px;
    font-style: italic;
    font-weight: 500;
    line-height: 35px;
  }
  .byline {
    position: absolute;
    left: 0;
    top: 1077px;
    width: 100%;
    margin: 0;
    text-align: center;
    color: var(--byline);
    font-size: 25px;
    font-weight: 500;
    letter-spacing: 0.25em;
    text-indent: 0.25em;
    line-height: 1;
  }
</style>
</head>
<body>
<main class="cover">
  <section class="noise-cloud" aria-label="Diet buzzwords">
    <p class="buzzword bold caps" style="left:100px;top:72px;font-size:22px;color:#999;transform:rotate(-10deg)">KETO</p>
    <p class="buzzword" style="left:327px;top:64px;font-size:31px;transform:rotate(5deg)">detox</p>
    <p class="buzzword" style="left:650px;top:74px;font-size:25px;transform:rotate(8deg)">paleo</p>
    <p class="buzzword faint caps" style="left:236px;top:128px;font-size:14px;transform:rotate(-3deg)">ANTIOXIDANTS</p>
    <p class="buzzword caps" style="left:476px;top:110px;font-size:15px;transform:rotate(-4deg)">GLUTEN-FREE</p>
    <p class="buzzword strong" style="left:134px;top:179px;font-size:41px;color:#aaa;transform:rotate(4deg)">superfood</p>
    <p class="buzzword faint caps" style="left:390px;top:192px;font-size:17px;transform:rotate(-18deg)">CLEAN EATING</p>
    <p class="buzzword strong" style="left:478px;top:196px;font-size:36px;color:#a8a8a8;transform:rotate(-7deg)">low-carb</p>
    <p class="buzzword faint caps" style="left:607px;top:245px;font-size:13px;transform:rotate(-22deg)">JUICE CLEANSE</p>
    <p class="buzzword" style="left:167px;top:247px;font-size:21px;transform:rotate(6deg)">organic</p>
    <p class="buzzword" style="left:322px;top:252px;font-size:27px;transform:rotate(3deg)">fat-burning</p>
    <p class="buzzword caps" style="left:536px;top:272px;font-size:17px;transform:rotate(9deg)">WHOLE21</p>
    <p class="buzzword strong" style="left:102px;top:304px;font-size:36px;transform:rotate(-5deg)">fasting</p>
    <p class="buzzword" style="left:323px;top:334px;font-size:20px;transform:rotate(-12deg)">calories in/out</p>
    <p class="buzzword faint caps" style="left:481px;top:342px;font-size:15px;transform:rotate(-6deg)">SUGAR-FREE</p>
    <p class="buzzword" style="left:645px;top:322px;font-size:23px;transform:rotate(4deg)">vegan</p>
    <p class="buzzword strong" style="left:206px;top:382px;font-size:31px;transform:rotate(6deg)">macros</p>
    <p class="buzzword faint caps" style="left:372px;top:382px;font-size:16px;transform:rotate(12deg)">ALKALINE</p>
    <p class="buzzword" style="left:502px;top:398px;font-size:20px;transform:rotate(-5deg)">lectin-free</p>
    <p class="buzzword" style="left:632px;top:382px;font-size:19px;transform:rotate(-4deg)">raw</p>
    <p class="buzzword" style="left:99px;top:441px;font-size:24px;transform:rotate(2deg)">carnivore</p>
    <p class="buzzword faint caps" style="left:321px;top:454px;font-size:14px;transform:rotate(-1deg)">INFLAMMATION</p>
    <p class="buzzword faint caps" style="left:512px;top:460px;font-size:12px;transform:rotate(-2deg)">BIOHACKING</p>
    <p class="buzzword faint caps" style="left:180px;top:520px;font-size:15px;transform:rotate(-6deg)">SUPERGREENS</p>
    <p class="buzzword faint" style="left:391px;top:508px;font-size:20px;transform:rotate(5deg)">adaptogens</p>
    <p class="buzzword faint" style="left:606px;top:514px;font-size:22px;transform:rotate(3deg)">gut health</p>
  </section>

  <div class="rule-wide" aria-hidden="true"></div>

  <p class="title-kicker">THE</p>
  <h1 class="title-main"><span>PLATE</span><span>COMPASS</span></h1>

  <div class="rule-short" aria-hidden="true"></div>

  <p class="subtitle">Cutting Through the Noise<br>to What Actually Works</p>

  <p class="byline">AUTHOR NAME</p>
</main>
</body>
</html>
```